New Innovative Counselling and psychotherapy Service needs Business Card design

Keep it simple and professional. On one side, just company name and logo (perhaps in all blue) and maybe a tag line.

On other side (all white) my name and Qualifications in centre

Industry/Entity Type

Health And Wellness

Contact Information for Business Card

Dara Whelby
Counsellor & Psychotherapist
BSc (Psychol.), BA, Dip. (Couns. & Psych.), PG.Cert (CBT), FGTrK, ONRE

I will also require Mobile no, Email and web site address of which I'll pass on to final designer.

Font styles to use
Sans Serif

Requirements
Must have
• My Logo Only and please use the colours in logo that is in it.
Should not have
• Any other images

```html
<!DOCTYPE html>
<html lang="en">
<head>
<meta charset="utf-8">
<title>Harbour Path – Business Card</title>
<link rel="stylesheet" href="https://fonts.googleapis.com/css2?family=Open+Sans:ital,wght@0,300;0,400;0,600;0,700;1,400&display=swap">
<style>
  :root {
    --backdrop: #3a322e;
    --card: #1b1b1c;
    --brand-blue: #4bb3ec;
    --brand-green: #8fd14f;
    --text-grey: #9a9a9c;
    --text-white: #f2f2f2;
    --divider: #4a4a4c;
  }
  * { box-sizing: border-box; margin: 0; padding: 0; }
  html, body {
    width: 1200px; height: 864px; overflow: hidden;
    background: var(--backdrop);
    font-family: "Open Sans", Arial, sans-serif;
  }
  .canvas {
    position: relative; width: 1200px; height: 864px;
    display: flex; align-items: center; justify-content: center; gap: 50px;
  }
  .card {
    width: 540px; height: 309px;
    background: var(--card);
    border-radius: 3px;
    box-shadow: 0 10px 30px rgba(0,0,0,.45);
    position: relative;
  }

  /* Front side */
  .card-front {
    display: flex; flex-direction: column; align-items: center; justify-content: center;
  }
  .brand {
    display: flex; align-items: center; gap: 16px;
  }
  .brand-dot {
    width: 46px; height: 46px; border-radius: 50%;
    background: var(--brand-blue);
  }
  .brand-name {
    font-weight: 300; font-size: 40px; color: var(--text-grey);
    letter-spacing: -0.5px;
  }
  .tagline {
    margin-top: 42px;
    font-style: italic; font-size: 14px; color: var(--text-grey);
  }

  /* Back side */
  .card-back {
    display: flex; align-items: center; padding-left: 54px;
  }
  .mark-block {
    display: flex; flex-direction: column; align-items: center; gap: 12px;
    width: 150px;
  }
  .mark-circle {
    width: 128px; height: 128px; border-radius: 50%;
    background: var(--brand-blue);
  }
  .mark-name {
    font-size: 15px; font-weight: 600; color: var(--brand-blue);
  }
  .divider {
    width: 1px; height: 150px; background: var(--divider);
    margin: 0 20px 0 22px;
  }
  .details { color: var(--text-white); }
  .person-name {
    font-weight: 700; font-size: 18px; color: var(--brand-blue);
    text-transform: uppercase; line-height: 1.1;
  }
  .person-role {
    font-size: 16px; color: var(--brand-green);
    text-transform: uppercase; line-height: 1.2;
  }
  .qualifications {
    font-size: 10.5px; color: var(--brand-green); line-height: 1.35;
    margin-top: 2px;
  }
  .contact-list { list-style: none; margin-top: 8px; }
  .contact-list li {
    display: flex; align-items: center; gap: 8px;
    font-size: 15px; line-height: 1.3; color: var(--text-white);
  }
  .contact-list svg { width: 12px; height: 12px; flex: none; }
</style>
</head>
<body>
<main class="canvas">

  <section class="card card-front" aria-label="Card front">
    <div class="brand">
      <span class="brand-dot"></span>
      <span class="brand-name">Harbour Path</span>
    </div>
    <p class="tagline">Caring For Your Psychological Well-Being Is Our Top Priority</p>
  </section>

  <section class="card card-back" aria-label="Card back">
    <div class="mark-block">
      <span class="mark-circle"></span>
      <span class="mark-name">Harbour Path</span>
    </div>
    <span class="divider"></span>
    <div class="details">
      <h1 class="person-name">Dara Whelby</h1>
      <h2 class="person-role">Counsellor &amp; Psychotherapist</h2>
      <p class="qualifications">BSc (Psychol.), BA, Dip. (Couns. &amp; Psych.)<br>PG.Cert (CBT), FGTrK.</p>
      <ul class="contact-list">
        <li>
          <svg viewBox="0 0 12 12" aria-hidden="true"><rect x="3" y="0.5" width="6" height="11" rx="1" fill="none" stroke="var(--brand-blue)" stroke-width="1.2"/><circle cx="6" cy="9.5" r="0.7" fill="var(--brand-blue)"/></svg>
          555 201 4478
        </li>
        <li>
          <svg viewBox="0 0 12 12" aria-hidden="true"><rect x="0.5" y="2.5" width="11" height="7.5" fill="var(--brand-blue)"/><path d="M0.5 2.5 L6 7 L11.5 2.5" fill="none" stroke="var(--card)" stroke-width="1"/></svg>
          dara@Harbourpath.com
        </li>
        <li>
          <svg viewBox="0 0 12 12" aria-hidden="true"><circle cx="6" cy="6" r="5.5" fill="var(--brand-blue)"/><path d="M0.5 6 H11.5 M6 0.5 C3.5 3 3.5 9 6 11.5 M6 0.5 C8.5 3 8.5 9 6 11.5" fill="none" stroke="var(--card)" stroke-width="0.8"/></svg>
          www.Harbourpath.com
        </li>
      </ul>
    </div>
  </section>

</main>
</body>
</html>
```